cryotherapy business . Whole Body Cryotherapy, Localised Cryotherapy, Cryofacials

Need home page plus services, about, pricing, online booking, contact and blog page

I want something slick, hip and professional. Our studio colours are duck egg blue, white and grey

I would also like a social media scroll at the bottom of every page

I will upload some web designs that I like the look of

Target Market(s)

Men and Women 25-45

Industry/Entity Type

Health And Wellness

Coding

Coded - Design and coding required

Number of Pages Required

5+ page

Font styles to use
Serif
Sans Serif

Requirements
Must have
• Must be eye catching and easy to navigate
Nice to have
• animation
Should not have
• Not sure what the site should not have. I am fairly open to ideas as this is a brand new business.

```html
<!DOCTYPE html>
<html lang="en">
<head>
<meta charset="utf-8">
<title>Frostline – Integrated Cryotherapy</title>
<link rel="stylesheet" href="https://fonts.googleapis.com/css2?family=Lato:wght@300;400;700;900&family=Montserrat:wght@200;300;400&display=swap">
<style>
:root{
  --duck:#9fc8d4;
  --duck-dark:#86b6c4;
  --blue:#0b3a8c;
  --blue-mid:#3569b3;
  --grey:#5d6470;
  --grey-text:#7a7a7a;
  --ink:#222;
  --dark:#3a3a3a;
  --white:#fff;
}
*{margin:0;padding:0;box-sizing:border-box}
html,body{width:1200px;height:3292px;overflow:hidden}
body{position:relative;background:var(--white);font-family:'Lato',sans-serif;color:var(--ink)}
.abs{position:absolute}

/* header */
.site-header{left:0;top:0;width:1200px;height:112px;background:var(--white)}
.brand{left:74px;top:36px;font-family:'Montserrat',sans-serif;font-weight:300;font-size:46px;letter-spacing:5px;color:#8a8a8a;line-height:1}
.main-nav{left:510px;top:45px;display:flex;gap:27px;font-size:14px;font-weight:700;color:var(--ink);letter-spacing:.2px}

/* hero */
.hero{left:0;top:112px;width:1200px;height:520px}
.hero-kicker{left:0;top:140px;width:1200px;text-align:center;color:#fff;font-size:18px;letter-spacing:3px;font-weight:400}
.hero-title{left:0;top:172px;width:1200px;text-align:center;color:#fff;font-family:'Montserrat',sans-serif;font-weight:200;font-size:176px;letter-spacing:14px;line-height:1}
.hero-sub{left:0;top:361px;width:1200px;text-align:center;color:#fff;font-size:18px;letter-spacing:5px}
.slider-dots{left:158px;top:461px;display:flex;gap:10px}
.slider-dots span{width:10px;height:10px;border-radius:50%;background:#222}
.slider-dots span.active{background:#e2577a}
.side-social{left:1146px;top:134px;display:flex;flex-direction:column;gap:16px}
.side-social span{width:40px;height:40px;border-radius:4px}

/* services */
.section-title{left:0;width:1200px;text-align:center;font-weight:900;color:var(--grey-text)}
.services-title{top:650px;font-size:46px;letter-spacing:1px}
.service-card{top:721px;width:335px;height:430px;overflow:hidden}
.service-photo{left:0;top:0;width:335px}
.service-panel{left:0;width:335px}
.card-open .service-panel{top:212px;height:218px;background:var(--duck);padding:40px 20px 0 24px}
.card-open h3{font-size:17px;font-weight:700;display:flex;align-items:center;gap:12px}
.card-open p{margin-top:22px;font-size:19px;line-height:30px;text-align:justify}
.toggle{width:34px;height:34px;border-radius:50%;background:#6f7d84;display:inline-flex;align-items:center;justify-content:center}
.card-closed .service-panel{top:360px;height:70px;background:var(--dark);color:#fff;display:flex;align-items:center;justify-content:space-between;padding:0 28px 0 26px}
.card-closed h3{font-size:17px;font-weight:700}
.play{width:36px;height:36px;border-radius:50%;background:#111;display:flex;align-items:center;justify-content:center}

/* about */
.about-title{left:102px;top:1215px;font-size:50px;font-weight:900;color:var(--grey-text)}
.about-sub{left:102px;top:1286px;font-size:24px;font-weight:700}
.about-copy{left:101px;top:1334px;width:462px;font-size:14.4px;line-height:27.7px;color:#444}
.btn{display:flex;align-items:center;justify-content:center;border-radius:22px;color:#fff;font-weight:900;font-size:17px;letter-spacing:.3px}
.btn-duck{background:var(--duck)}
.btn-dark{background:var(--dark)}
.about-btn{left:95px;top:1545px;width:147px;height:44px}
.collage{left:618px;top:1214px;width:480px;height:332px}

/* booking */
.booking-bg{left:0;top:1600px;width:1200px;height:649px}
.booking-title{top:1762px;font-size:48px;color:#fff}
.booking-note{left:0;top:1833px;width:1200px;text-align:center;color:#fff;font-size:14.5px;line-height:28px}
.field{background:#fff;font-size:14px;color:#444;padding:0 11px;display:flex;align-items:center}
.field-area{align-items:flex-start;padding-top:11px}
.submit-btn{left:553px;top:2142px;width:149px;height:44px}

/* blog */
.blog{left:0;top:2249px;width:1200px;height:642px;background:var(--duck)}
.blog-title{top:2322px;font-size:33px;color:#fff}
.post{top:2422px;width:331px}
.post-photo{width:331px;height:198px;position:relative}
.post-share{position:absolute;right:22px;bottom:10px;display:flex;gap:4px}
.post-share span{width:34px;height:34px;border-radius:50%;background:#1f3fb0}
.post-comments{position:absolute;left:22px;bottom:18px;color:#fff;font-size:14px;display:flex;gap:8px;align-items:center}
.post h4{margin-top:30px;font-size:19px;font-weight:400;color:#444;letter-spacing:.3px}
.post p{margin-top:9px;font-size:14.5px;line-height:29px;color:#444}
.post .btn{margin-top:14px;width:147px;height:44px;border-radius:22px}

/* footer */
.footer-brand{left:0;top:2948px;width:1200px;text-align:center;font-family:'Montserrat',sans-serif;font-weight:300;font-size:46px;letter-spacing:5px;color:#8a8a8a}
.footer-nav{left:0;top:3035px;width:1200px;display:flex;justify-content:center;gap:27px;font-size:14px;font-weight:700}
.newsletter{left:449px;top:3090px;width:302px;height:40px;display:flex;border:1px solid #bbb}
.newsletter span{flex:1;font-size:14px;color:#444;display:flex;align-items:center;padding-left:9px}
.newsletter b{width:52px;background:var(--grey);color:#fff;display:flex;align-items:center;justify-content:center;font-size:16px}
.footer-social{left:0;top:3174px;width:1200px;display:flex;justify-content:center;gap:34px}
.footer-social span{width:24px;height:24px;background:#111;border-radius:3px}
.copyright{left:0;top:3226px;width:1200px;text-align:center;font-size:13px;color:#333}
</style>
</head>
<body>

<header class="abs site-header">
  <div class="abs brand">FROSTLINE</div>
  <nav class="abs main-nav">
    <span>HOME</span><span>SERVICES</span><span>ABOUT</span><span>PRICING</span><span>ONLINE BOOKING</span><span>CONTACT</span><span>BLOG</span>
  </nav>
</header>

<svg class="abs hero" viewBox="0 0 1200 520" role="img" aria-label="Photo of cold blue vapour swirling across the banner">
  <defs>
    <linearGradient id="heroGrad" x1="0" y1="0" x2="1" y2="1">
      <stop offset="0" stop-color="#0b3a8c"/>
      <stop offset=".55" stop-color="#2a5fae"/>
      <stop offset="1" stop-color="#7fa3d3"/>
    </linearGradient>
  </defs>
  <path d="M0,0 H1200 V406 C1050,470 880,515 640,508 C470,503 330,450 170,455 C80,458 30,430 0,380 Z" fill="url(#heroGrad)"/>
</svg>
<div class="abs hero-kicker">THE POWER OF</div>
<div class="abs hero-title">COLD</div>
<div class="abs hero-sub">INTEGRATED CRYOTHERAPY</div>
<div class="abs slider-dots"><span></span><span class="active"></span><span></span><span></span></div>
<div class="abs side-social" aria-label="Social links">
  <span style="background:#0b3a8c"></span>
  <span style="background:#1da1d8"></span>
  <span style="background:#0b3a8c"></span>
  <span style="background:#d81b78"></span>
</div>

<h2 class="abs section-title services-title">OUR SERVICES</h2>

<article class="abs service-card card-open" style="left:74px">
  <div class="abs service-photo" style="height:212px;background:linear-gradient(160deg,#2a3fd1,#6d86d8 60%,#c9b8a8)" role="img" aria-label="Photo of a woman inside a whole body cryotherapy chamber"></div>
  <div class="abs service-panel">
    <h3>WHOLE BODY CRYOTHERAPY <span class="toggle"><svg width="14" height="10" viewBox="0 0 14 10"><path d="M1 1 L7 8 L13 1 Z" fill="#fff"/></svg></span></h3>
    <p>Nam libero tempore, cum soluta nobis est eligendi optio cumque nihil impedit quo minus id quod.</p>
  </div>
</article>

<article class="abs service-card card-closed" style="left:433px">
  <div class="abs service-photo" style="height:360px;background:linear-gradient(150deg,#e9edf2,#c9a58e 55%,#3d6fb5)" role="img" aria-label="Photo of a woman receiving localised cryotherapy on her neck"></div>
  <div class="abs service-panel">
    <h3>LOCALISED CRYOTHERAPY</h3>
    <span class="play"><svg width="12" height="14" viewBox="0 0 12 14"><path d="M2 1 L11 7 L2 13 Z" fill="#fff"/></svg></span>
  </div>
</article>

<article class="abs service-card card-closed" style="left:791px">
  <div class="abs service-photo" style="height:360px;background:linear-gradient(150deg,#8fb9e6,#e6cbb8 50%,#f1f1f1)" role="img" aria-label="Photo of a woman receiving a cryofacial treatment"></div>
  <div class="abs service-panel">
    <h3>CRYOFACIALS</h3>
    <span class="play"><svg width="12" height="14" viewBox="0 0 12 14"><path d="M2 1 L11 7 L2 13 Z" fill="#fff"/></svg></span>
  </div>
</article>

<h2 class="abs about-title">ABOUT US</h2>
<h3 class="abs about-sub">WHAT IS CRYOTHERAPY?</h3>
<p class="abs about-copy">Originally invented by doctors as a powerful anti-inflammatory tool, cryotherapy is a quick, noninvasive process that exposes your body to extreme cold of up to -250°F. This sudden drop in temperature increases circulation and pumps reoxygenated and nutrient enriched blood back into the bloodstream reducing pain &amp; inflammation and alleviating sore muscles. It’s also known to release ‘feel good’ endorphins that help improve sleep, reduce stress, and increase your metabolism.</p>
<div class="abs btn btn-duck about-btn">READ MORE</div>

<svg class="abs" style="left:600px;top:1480px" width="600" height="200" viewBox="0 0 600 200" aria-hidden="true">
  <path d="M30,30 C120,40 200,20 300,40 C400,60 480,20 600,0 V185 C520,200 420,160 340,110 C260,70 120,80 30,60 C5,50 5,30 30,30 Z" fill="var(--duck)"/>
</svg>
<div class="abs collage" role="img" aria-label="Collage of a client in a cryotherapy chamber, an athlete with a belt, and the chamber unit" style="background:linear-gradient(120deg,rgba(60,90,200,.15),#3b5ed6 45%,#b7bfc8 75%,rgba(230,230,230,.2));clip-path:polygon(0 45%,20% 25%,45% 10%,60% 0,95% 0,100% 55%,80% 100%,40% 100%,30% 78%,12% 70%)"></div>

<svg class="abs booking-bg" viewBox="0 0 1200 649" role="img" aria-label="Misty grey photo backdrop behind the booking form">
  <defs>
    <linearGradient id="bookGrad" x1="0" y1="0" x2="1" y2="1">
      <stop offset="0" stop-color="#5a616d"/>
      <stop offset=".5" stop-color="#6b727d"/>
      <stop offset="1" stop-color="#555c68"/>
    </linearGradient>
  </defs>
  <path d="M0,170 C110,90 280,95 440,70 C560,48 620,22 820,24 C980,27 1100,80 1200,122 V649 H0 Z" fill="url(#bookGrad)"/>
</svg>
<h2 class="abs section-title booking-title">ONLINE BOOKING</h2>
<p class="abs booking-note">Please arrive at least 5 minutes early to your scheduled appointment.<br>We value each of our clients’ schedule and time.</p>
<div class="abs field" style="left:281px;top:1913px;width:334px;height:47px">Enter Name</div>
<div class="abs field" style="left:642px;top:1913px;width:333px;height:47px">Subject</div>
<div class="abs field" style="left:281px;top:1973px;width:693px;height:47px">Enter Email Address</div>
<div class="abs field field-area" style="left:281px;top:2032px;width:693px;height:87px">Message</div>
<div class="abs btn btn-duck submit-btn">SUBMIT</div>

<section class="abs blog"></section>
<h2 class="abs section-title blog-title">BLOG</h2>

<article class="abs post" style="left:74px">
  <div class="post-photo" role="img" aria-label="Photo of a man relaxing in a cryotherapy chamber" style="background:linear-gradient(135deg,#c9641f,#e9b85a 50%,#f4efe2)">
    <div class="post-share"><span></span><span style="background:#1da1f2"></span><span></span></div>
  </div>
  <h4>LOREM IPSUM DOLOR</h4>
  <p>Sed ut perspiciatis unde omnis iste natus error sit voluptatem accusantium doloremque laudantium, totam rem aperiam,</p>
  <div class="btn btn-dark">READ MORE</div>
</article>

<article class="abs post" style="left:436px">
  <div class="post-photo" role="img" aria-label="Photo of a woman in a cryotherapy chamber" style="background:linear-gradient(135deg,#3b4150,#c89c78 50%,#5a6070)">
    <div class="post-comments"><svg width="20" height="16" viewBox="0 0 20 16"><path d="M10 1C5 1 1 4 1 7.5c0 2 1.2 3.6 3 4.7L3 15l4-2c1 .2 2 .3 3 .3 5 0 9-3 9-6.5S15 1 10 1z" fill="none" stroke="#fff" stroke-width="1.5"/></svg>23</div>
    <div class="post-share"><span></span><span style="background:#1da1f2"></span><span></span></div>
  </div>
  <h4>LOREM IPSUM DOLOR</h4>
  <p>Sed ut perspiciatis unde omnis iste natus error sit voluptatem accusantium doloremque laudantium, totam rem aperiam,</p>
  <div class="btn btn-dark">READ MORE</div>
</article>

<article class="abs post" style="left:796px">
  <div class="post-photo" role="img" aria-label="Photo of a smiling swimmer after a cryotherapy session" style="background:linear-gradient(135deg,#2f3a55,#b48a6c 45%,#e8eef6)">
    <div class="post-comments"><svg width="20" height="16" viewBox="0 0 20 16"><path d="M10 1C5 1 1 4 1 7.5c0 2 1.2 3.6 3 4.7L3 15l4-2c1 .2 2 .3 3 .3 5 0 9-3 9-6.5S15 1 10 1z" fill="none" stroke="#fff" stroke-width="1.5"/></svg>23</div>
    <div class="post-share"><span></span><span style="background:#1da1f2"></span><span></span></div>
  </div>
  <h4>LOREM IPSUM DOLOR</h4>
  <p>Sed ut perspiciatis unde omnis iste natus error sit voluptatem accusantium doloremque laudantium, totam rem aperiam,</p>
  <div class="btn btn-dark">READ MORE</div>
</article>

<footer>
  <div class="abs footer-brand">FROSTLINE</div>
  <nav class="abs footer-nav">
    <span>HOME</span><span>SERVICES</span><span>ABOUT</span><span>PRICING</span><span>ONLINE BOOKING</span><span>CONTACT</span><span>BLOG</span>
  </nav>
  <div class="abs newsletter"><span>Enter Email Address</span><b>GO</b></div>
  <div class="abs footer-social" aria-label="Social links"><span></span><span></span><span></span><span></span><span></span></div>
  <div class="abs copyright">©2019 www.companyname.com</div>
</footer>

</body>
</html>
```